Employment Agency Website Design

We are working with an employment agency in California.

Some sites to use for content/competitors and inspiration:

https://www.pinecrestjobs.com/us/en
https://www.velmorusa.com
https://www.dravenworks.us
https://www.quillora.com/en
https://www.tomvalusa.com
https://www.fernstaffing.com

Thank you for taking the time to consider designing a website for us. We are web developers based in Stockton, CA, USA. Most of our projects go through the same process. Understanding this process may help you win a project with us. We custom-code all of our websites in-house. We don’t have any requirements as to what tools you use for your design, but we prefer Figma files. For any design that we label as four-stars, we send it to the client for review. The client picks the final design they want us to use. Once we complete this process, we will continue to show additional clients all the four-star sites and purchase them later. Your designs will have multiple chances to sell. For better chances of success, we ask that you follow these guidelines.

IMAGES:
If you use any images or icons in the design, we ask that you have a link to the asset so we can purchase the image/icon. Most of the designs we submit do not have the customer’s images on them unless they have some great images. Be creative; show us the feeling you are trying to portray with your image choices. Use any royalty-free site you choose. We subscribe to Adobe and mainly use their images, but we can purchase images outside of Adobe. PLEASE NOTE: we will not submit designs to clients with watermarks on the images.

FONTS:
We ask that you identify the fonts used in the design. This can be done in a message if you want. We typically use Google Fonts and Adobe Fonts.

CONTENT:
We're always open to different content and ideas. We often submit designs with stock images so the client can see our vision. We typically take pictures after the website launch to use their images with our vision. Lorem Ipsum is fine for paragraphs, but we ask that you write the headers in correct English. We want to be able to show the vision and identify the sections of the website.

INSPIRATION:
We typically add a couple of links in the brief of websites we like to help you get started in your design.

REVISIONS:
We do not often ask for revisions of the designs unless we see something in the design that may not appeal to the client. If there are slight changes that we want to make, we do that in the development process.

FEEDBACK:
We rarely give feedback on designs during the design process. We are working on many website projects and do not have the time to provide feedback. We usually respond if your request is well thought out and asks specific questions, but a note asking “feedback, please” usually goes unanswered.

```html
<!DOCTYPE html>
<html lang="en">
<head>
<meta charset="utf-8">
<title>Kestrel Talent – Employment Agency</title>
<link href="https://fonts.googleapis.com/css2?family=Roboto:wght@400;500;700;900&display=swap" rel="stylesheet">
<style>
:root{
  --red:#b81c2b;
  --red-dark:#8e1320;
  --ink:#111111;
  --dark:#1a0c0e;
  --grey:#7a7a7a;
  --light:#f1f1f1;
  --footer:#151515;
  --white:#ffffff;
}
*{box-sizing:border-box;margin:0;padding:0}
html,body{width:1200px;height:4959px;overflow:hidden}
body{font-family:"Roboto",Arial,sans-serif;color:var(--ink);background:var(--white);position:relative}
.abs{position:absolute}
.underline{display:block;width:70px;height:4px;background:var(--red)}
.photo{position:absolute}
/* top bar */
.topbar{top:0;left:0;width:1200px;height:40px;background:#0e0e0e;color:var(--white);font-size:12.5px}
.topbar .contact{left:112px;top:12px;display:flex;gap:14px;align-items:center}
.topbar .contact span{display:flex;align-items:center;gap:7px}
.topbar .social{right:112px;top:12px;display:flex;gap:22px}
.dot-icon{width:14px;height:14px;border-radius:50%;background:var(--white);display:block}
/* header */
.header{top:40px;left:0;width:1200px;height:118px;background:var(--white)}
.brand{display:flex;align-items:center;gap:12px}
.brand .mark{width:36px;height:36px;background:var(--red);display:block}
.brand .name{font-size:30px;font-weight:500;color:var(--ink);line-height:1;white-space:nowrap}
.header .brand{position:absolute;left:112px;top:41px}
.nav{position:absolute;left:505px;top:52px;display:flex;gap:26px;font-size:13.5px;font-weight:700}
.nav .active{color:var(--red)}
.login{position:absolute;left:973px;top:37px;width:115px;height:48px;background:var(--red);color:var(--white);font-size:13.5px;font-weight:700;display:flex;align-items:center;justify-content:center;gap:8px}
/* hero */
.hero{top:158px;left:0;width:1200px;height:643px}
.hero .photo{inset:0;background:linear-gradient(100deg,#d9d4cc 0%,#bdb3a6 35%,#6b6560 65%,#4a4a4f 100%)}
.hero .welcome{left:111px;top:214px;color:var(--red);font-size:23px;font-weight:700}
.hero h1{left:110px;top:248px;font-size:40px;font-weight:700;color:var(--ink)}
.hero p{left:111px;top:304px;width:470px;font-size:15.5px;line-height:27px;color:var(--ink)}
.btn{display:flex;align-items:center;justify-content:center;font-size:13px;font-weight:700;text-transform:uppercase}
.hero .btn-red{left:112px;top:379px;width:180px;height:44px;background:var(--red);color:var(--white)}
.hero .btn-white{left:300px;top:379px;width:180px;height:44px;background:var(--white);color:var(--ink)}
.slider-dots{left:1136px;top:275px;display:flex;flex-direction:column;gap:20px;align-items:center}
.slider-dots i{display:block;width:7px;height:7px;border-radius:50%;background:var(--white)}
.slider-dots i.on{width:16px;height:16px;border:3px solid var(--white);background:var(--red)}
/* section titles */
.section-title{position:absolute;left:0;width:1200px;text-align:center;font-size:40px;font-weight:700}
.section-title .underline{margin:10px auto 0}
/* how it works */
.card{top:1017px;width:305px;height:370px;background:var(--white);box-shadow:0 4px 18px rgba(0,0,0,.14);text-align:center;padding:40px 28px 0}
.card.featured{background:linear-gradient(120deg,#1a0a0c 0%,#6e121d 50%,#c01f2f 100%);color:var(--white)}
.card h3{font-size:17px;font-weight:700;line-height:27px;margin-top:18px}
.card .underline{width:36px;height:3px;margin:10px auto 14px}
.card.featured .underline{background:var(--white)}
.card p{font-size:14px;line-height:26px;color:var(--grey)}
.card.featured p{color:var(--white)}
.hex{display:block;margin:0 auto}
/* split sections */
.split-text{left:660px;width:428px}
.split-text h2{font-size:32px;font-weight:700;line-height:38px}
.split-text .underline{margin:14px 0 28px;width:74px}
.split-text p{font-size:14.5px;line-height:26.5px;color:var(--grey);text-align:justify;margin-bottom:12px}
.btn-dark{width:136px;height:46px;background:linear-gradient(90deg,#160c0d,#a31a28);color:var(--white);margin-top:30px}
.dots-grid{background-image:radial-gradient(circle,#c9c9c9 2px,transparent 2.5px);background-size:13px 13px}
/* direct hire */
.band{top:2053px;left:0;width:1200px;height:505px;background:linear-gradient(90deg,#1b0b0d 0%,#5d0f18 40%,#a51b29 70%,#c2273a 100%)}
.band .content{left:132px;top:78px;width:490px;color:var(--white)}
.band h2{font-size:33px;font-weight:700}
.band .underline{background:var(--white);margin:10px 0 28px;width:74px}
.band p{font-size:14.5px;line-height:26.5px;text-align:justify}
.btn-white-sm{width:136px;height:45px;background:var(--white);color:var(--ink);margin-top:30px}
/* blog */
.blog{top:3290px;left:0;width:1200px;height:678px;background:var(--light)}
.post{background:var(--white);box-shadow:0 3px 12px rgba(0,0,0,.08)}
.meta{display:flex;align-items:center;gap:10px;font-size:11px;color:var(--ink)}
.meta i{display:block;width:22px;height:22px;border-radius:50%;background:#e2e2e2}
.post h3{font-size:16px;font-weight:700;line-height:24px;text-transform:uppercase}
.post p{font-size:12.5px;line-height:23px;color:var(--grey)}
.read{font-size:12.5px;font-weight:700;color:var(--red);text-decoration:underline}
/* testimonial */
.testi{left:292px;top:4179px;width:713px;height:299px;background:var(--white);box-shadow:0 4px 22px rgba(0,0,0,.13)}
.avatar{left:195px;top:4234px;width:176px;height:176px;border-radius:50%;background:linear-gradient(160deg,#dcd9d5,#7d8ea3);border:10px solid var(--white);box-shadow:0 3px 16px rgba(0,0,0,.18)}
.testi p{position:absolute;left:140px;top:58px;width:530px;font-size:17px;line-height:30px;color:var(--grey)}
.testi .who{position:absolute;left:140px;top:190px;font-size:21px;font-weight:700}
.testi .who small{font-size:14px;font-weight:400}
.stars{position:absolute;left:140px;top:220px;color:#f0a500;font-size:14px;letter-spacing:2px}
/* footer */
.footer{top:4599px;left:0;width:1200px;height:360px;background:var(--footer);color:var(--white)}
.footer .brand .name{color:var(--white);font-size:26px}
.footer .brand .mark{width:30px;height:30px}
.f-info{font-size:13.5px;line-height:21px}
.f-row{display:flex;gap:18px;align-items:flex-start}
.f-row svg{flex:none;margin-top:4px}
.f-head{font-size:15.5px;font-weight:700}
.links{display:grid;grid-template-columns:165px 150px;row-gap:12px;font-size:13.5px}
.links span{display:flex;align-items:center;gap:14px}
.bullet{width:12px;height:12px;border-radius:50%;background:var(--red);display:block}
.subscribe{left:805px;top:119px;width:283px;height:46px;background:var(--white);display:flex;align-items:center;justify-content:space-between;padding-left:18px;color:#888;font-size:13px}
.subscribe b{width:46px;height:46px;background:var(--red);display:flex;align-items:center;justify-content:center;border:3px solid var(--white)}
.f-social{left:805px;top:199px;display:flex;gap:8px}
.f-social i{display:block;width:34px;height:34px;border-radius:50%;border:2px solid var(--white)}
.f-social i:first-child{background:var(--red);border-color:var(--red)}
.copy{left:0;top:327px;width:1200px;text-align:center;font-size:12px}
</style>
</head>
<body>

<div class="abs topbar">
  <div class="abs contact">
    <span><svg width="11" height="11" viewBox="0 0 24 24"><path fill="#b81c2b" d="M6.6 10.8a15 15 0 006.6 6.6l2.2-2.2a1 1 0 011-.25 11.4 11.4 0 003.6.6 1 1 0 011 1V20a1 1 0 01-1 1A17 17 0 013 4a1 1 0 011-1h3.5a1 1 0 011 1c0 1.25.2 2.45.57 3.57a1 1 0 01-.25 1z"/></svg>+1 (209) 555 0148</span>
    <span>|</span>
    <span><svg width="12" height="10" viewBox="0 0 24 18"><path fill="#b81c2b" d="M0 0h24v18H0z"/><path fill="none" stroke="#0e0e0e" stroke-width="2" d="M1 1l11 9 11-9"/></svg>info@kestreltalent.com</span>
  </div>
  <div class="abs social"><i class="dot-icon"></i><i class="dot-icon"></i><i class="dot-icon"></i><i class="dot-icon"></i></div>
</div>

<header class="abs header">
  <div class="brand"><span class="mark"></span><div class="name">Kestrel Talent</div></div>
  <nav class="nav"><span class="active">HOME</span><span>ABOUT</span><span>SERVICES</span><span>RESOURCES</span><span>CONTACT US</span></nav>
  <div class="login"><svg width="12" height="12" viewBox="0 0 24 24"><circle cx="12" cy="7" r="5" fill="#fff"/><path d="M2 24a10 10 0 0120 0z" fill="#fff"/></svg>LOGIN</div>
</header>

<section class="abs hero">
  <div class="photo" role="img" aria-label="Smiling young professional at a desk with laptop, desk lamp and plant"></div>
  <div class="abs welcome">WELCOME TO</div>
  <h1 class="abs">KESTREL TALENT</h1>
  <p class="abs">Lorem ipsum dolor sit amet consectetur adipiscing elit sed do eiusmod tempor incididea.</p>
  <div class="abs btn btn-red">Find Your Next Job</div>
  <div class="abs btn btn-white">Find Your Next Hire</div>
  <div class="abs slider-dots"><i></i><i class="on"></i><i></i><i></i></div>
</section>

<h2 class="section-title" style="top:912px">HOW IT WORKS<span class="underline"></span></h2>

<div class="abs card" style="left:112px">
  <svg class="hex" width="82" height="92" viewBox="0 0 82 92"><path d="M41 0l41 23v46L41 92 0 69V23z" fill="#7e1420"/><path d="M28 52h26v6H28zM34 36h14v14H34z" fill="#fff"/></svg>
  <h3>LOREM IPSUM DOLOR SIT AMET CONSEA</h3><span class="underline"></span>
  <p>Sed ut perspiciatis unde omnis iste natus error sit voluptatem accus an tium doloremque laudantium, totam apemque laudantira.</p>
</div>
<div class="abs card featured" style="left:447px">
  <svg class="hex" width="82" height="92" viewBox="0 0 82 92"><path d="M41 0l41 23v46L41 92 0 69V23z" fill="#fff"/><rect x="27" y="30" width="22" height="30" fill="none" stroke="#8e1320" stroke-width="3"/><circle cx="52" cy="56" r="7" fill="none" stroke="#b81c2b" stroke-width="3"/></svg>
  <h3>LOREM IPSUM DOLOR SIT AMET CONSEA</h3><span class="underline"></span>
  <p>Sed ut perspiciatis unde omnis iste natus error sit voluptatem accus an tium doloremque laudantium, totam apemque laudantira.</p>
</div>
<div class="abs card" style="left:783px">
  <svg class="hex" width="82" height="92" viewBox="0 0 82 92"><path d="M41 0l41 23v46L41 92 0 69V23z" fill="#7e1420"/><circle cx="41" cy="40" r="8" fill="#fff"/><path d="M24 62c5-8 29-8 34 0" stroke="#fff" stroke-width="3" fill="none"/></svg>
  <h3>LOREM IPSUM DOLOR SIT AMET CONSEA</h3><span class="underline"></span>
  <p>Sed ut perspiciatis unde omnis iste natus error sit voluptatem accus an tium doloremque laudantium, totam apemque laudantira.</p>
</div>

<div class="abs dots-grid" style="left:490px;top:1500px;width:122px;height:125px"></div>
<div class="abs" style="left:112px;top:1780px;width:166px;height:167px;border:3px solid var(--red)"></div>
<div class="photo" style="left:142px;top:1533px;width:435px;height:384px;background:var(--white);box-shadow:0 4px 16px rgba(0,0,0,.15)"></div>
<div class="photo" role="img" aria-label="Two colleagues reviewing documents and a tablet in an office" style="left:149px;top:1540px;width:421px;height:370px;background:linear-gradient(120deg,#6a7482,#b7a99a 55%,#e4dfd8)"></div>
<div class="abs split-text" style="top:1546px">
  <h2>FIND TALENT TO GET<br>MORE DONE</h2><span class="underline"></span>
  <p>Lorem ipsum dolor sit amet, consectetur adipiscing elit, sed do eiusmod tempor incididunt ut labore et dolore magna aliqua. Ut enim ad minim veniam, quis nostrud exercitation ullamco laboris nisi ut aliquip ex ea commodo consequat. Duis aute irure dolor in reprehenderit in voluptate velit esse cillum dolore eu fugiat nulla pariaturea.</p>
  <div class="btn btn-dark">Learn More</div>
</div>

<section class="abs band">
  <div class="abs content">
    <h2>DIRECT HIRE</h2><span class="underline"></span>
    <p>Lorem ipsum dolor sit amet, consectetur adipiscing elit, sed do eiusmod tempor incididunt ut labore et dolore magna aliqua. Ut enim ad minim veniam, quis nostrud exercitation ullamco laboris nisi ut aliquip ex ea commodo consequat. Duis aute irure dolor in reprehenderit in voluptate velit esse cillum dolore eu fugiat nulla pariatur excepteur sint occaecat cupidatat non proident, sunt in cuvoluptate velit esse cillum dolorelpea.</p>
    <div class="btn btn-white-sm">Learn More</div>
  </div>
</section>

<div class="photo" role="img" aria-label="Business people shaking hands" style="left:112px;top:2700px;width:343px;height:385px;background:linear-gradient(130deg,#3b4a63,#8c8d91 50%,#d9d3cb)"></div>
<div class="abs dots-grid" style="left:172px;top:3090px;width:135px;height:52px"></div>
<div class="photo" style="left:308px;top:2862px;width:290px;height:311px;background:var(--white)"></div>
<div class="photo" role="img" aria-label="Recruiter interviewing a candidate across a table" style="left:318px;top:2872px;width:272px;height:293px;background:linear-gradient(150deg,#c9c7c3,#a9a29a 50%,#3e4048)"></div>
<div class="abs split-text" style="top:2728px">
  <h2>TEMPORARY STAFFING</h2><span class="underline"></span>
  <p>Lorem ipsum dolor sit amet, consectetur adipiscing elit, sed do eiusmod tempor incididunt ut labore et dolore magna aliqua. Ut enim ad minim veniam, quis nostrud exercitation ullamco laboris nisi ut aliquipea.</p>
  <p>Lorem ipsum dolor sit amet, consectetur adipiscing elit, sed do eiusmod tempor incididunt ut labore et dolore magna aliqua. Ut enim ad minim veniam, quis nostrud exercitation ullamco laboris nisi ut aliquipea qui officia deserunt mollit anim id est laborumea.</p>
  <div class="btn btn-dark">Learn More</div>
</div>

<section class="abs blog">
  <h2 class="section-title" style="top:58px">LATEST BLOG POST<span class="underline"></span></h2>
  <article class="abs post" style="left:112px;top:159px;width:478px;height:446px">
    <div class="photo" role="img" aria-label="Smiling colleagues in a meeting" style="left:8px;top:8px;width:462px;height:283px;background:linear-gradient(120deg,#8c8a86,#d7d2cb 50%,#4b4f58)"></div>
    <div class="abs" style="left:20px;top:306px;width:430px">
      <div class="meta"><i></i>01 Mar 2024</div>
      <h3 style="margin-top:14px">Lorem ipsum dolor sit amet consectetur adipiscing elit sedea</h3>
      <div class="read" style="margin-top:14px">READ MORE</div>
    </div>
  </article>
  <article class="abs post" style="left:610px;top:159px;width:478px;height:212px">
    <div class="photo" role="img" aria-label="Team discussion around a boardroom table" style="left:7px;top:7px;width:198px;height:198px;background:linear-gradient(140deg,#3d5570,#a8a39c 60%,#e0dbd2)"></div>
    <div class="abs" style="left:225px;top:28px;width:235px">
      <div class="meta"><i></i>01 Mar 2024</div>
      <h3 style="margin-top:10px">Lorem ipsum dolor sit amet consea</h3>
      <p style="margin-top:6px">Lorem ipsum dolor sit amet consec tetur adipiscing elit sedea.</p>
      <div class="read" style="margin-top:8px">READ MORE</div>
    </div>
  </article>
  <article class="abs post" style="left:610px;top:392px;width:478px;height:213px">
    <div class="photo" role="img" aria-label="Professionals shaking hands in an office" style="left:7px;top:7px;width:198px;height:199px;background:linear-gradient(140deg,#c9c6c1,#7a766f 55%,#2f3138)"></div>
    <div class="abs" style="left:225px;top:28px;width:235px">
      <div class="meta"><i></i>01 Mar 2024</div>
      <h3 style="margin-top:10px">Lorem ipsum dolor sit amet consea</h3>
      <p style="margin-top:6px">Lorem ipsum dolor sit amet consec tetur adipiscing elit sedea.</p>
      <div class="read" style="margin-top:8px">READ MORE</div>
    </div>
  </article>
</section>

<h2 class="section-title" style="top:4074px">TESTIMONIALS<span class="underline"></span></h2>
<svg class="abs" style="left:64px;top:4310px" width="48" height="24" viewBox="0 0 48 24"><path d="M47 12H3M13 2L3 12l10 10" fill="none" stroke="#999" stroke-width="2.5"/></svg>
<svg class="abs" style="left:1088px;top:4310px" width="48" height="24" viewBox="0 0 48 24"><path d="M1 12h44M35 2l10 10-10 10" fill="none" stroke="#999" stroke-width="2.5"/></svg>
<div class="abs testi">
  <p>Lorem ipsum dolor sit amet, consectetur adipiscing elit, sed do eiusmod tempor incididunt ut labore et dolore magna aliqua. Ut enim ad minim veniam, quis nostrud exercitation ullamco laboris nisi ut aliquipea.</p>
  <div class="who">- DANIEL MOORE, <small>United States</small></div>
  <div class="stars">★★★★★</div>
  <svg class="abs" style="left:605px;top:205px" width="50" height="38" viewBox="0 0 50 38"><path d="M0 38V18C0 6 8 0 20 0v8c-6 0-10 3-10 10h10v20zM28 38V18C28 6 36 0 48 0v8c-6 0-10 3-10 10h10v20z" fill="#e4e4e4"/></svg>
</div>
<div class="abs avatar" role="img" aria-label="Portrait of the client giving the testimonial"></div>

<footer class="abs footer">
  <div class="abs brand" style="left:112px;top:68px"><span class="mark"></span><div class="name">Kestrel Talent</div></div>
  <div class="abs f-info" style="left:112px;top:136px;width:270px;display:flex;flex-direction:column;gap:16px">
    <div class="f-row"><svg width="10" height="14" viewBox="0 0 10 14"><path d="M5 0a5 5 0 015 5c0 4-5 9-5 9S0 9 0 5a5 5 0 015-5z" fill="#b81c2b"/></svg><span>218 Harbor Street, Stockton,<br>California</span></div>
    <div class="f-row"><svg width="11" height="11" viewBox="0 0 24 24"><path fill="#b81c2b" d="M6.6 10.8a15 15 0 006.6 6.6l2.2-2.2a1 1 0 011-.25 11.4 11.4 0 003.6.6 1 1 0 011 1V20a1 1 0 01-1 1A17 17 0 013 4a1 1 0 011-1h3.5a1 1 0 011 1c0 1.25.2 2.45.57 3.57a1 1 0 01-.25 1z"/></svg><span>+1 (209) 555 0148</span></div>
    <div class="f-row"><svg width="12" height="10" viewBox="0 0 24 18"><path fill="#b81c2b" d="M0 0h24v18H0z"/></svg><span>info@kestreltalent.com</span></div>
  </div>
  <div class="abs" style="left:405px;top:69px;width:1px;height:222px;background:#444"></div>
  <div class="abs f-head" style="left:455px;top:67px">LINKS</div>
  <div class="abs links" style="left:455px;top:112px">
    <span><i class="bullet"></i>Home</span><span><i class="bullet"></i>FAQ</span>
    <span><i class="bullet"></i>About</span><span><i class="bullet"></i>Site Map</span>
    <span><i class="bullet"></i>Services</span><span><i class="bullet"></i>Privacy Policy</span>
    <span><i class="bullet"></i>Resources</span><span><i class="bullet"></i>Terms Of Use</span>
    <span><i class="bullet"></i>Contact Us</span>
  </div>
  <div class="abs f-head" style="left:805px;top:67px">SUBSCRIBE FOR UPDATES</div>
  <div class="abs subscribe">Email Address<b><svg width="18" height="18" viewBox="0 0 24 24"><path d="M2 12L22 3l-6 19-4-8z" fill="none" stroke="#fff" stroke-width="2"/></svg></b></div>
  <div class="abs f-social"><i></i><i></i><i></i><i></i></div>
  <div class="abs" style="left:112px;top:317px;width:976px;height:1px;background:#3a3a3a"></div>
  <div class="abs copy">© 2024 <b>KESTREL TALENT</b> &nbsp;|&nbsp; All Rights Reserved</div>
</footer>

</body>
</html>
```